Coastal Learner Bureau business cards

Australian company about to start offering its services. We recruit international students to come to study English, vocational education and postgraduate courses in Australia. We help them find the institution and select the right city they want to come to Australia. We are a young, online oriented and supportive agency. Our clients are between 18 and 35 years old, mainly University students, young professionals or people with work experience. We provide much more information that any other agency offer. We administrate a Facebook group with more than 11.000 members that daily ask questions about general information when coming to Australia, while they are here and even after they leave the country

Target Market(s)

International students from South America, Central America and Europe

Industry/Entity Type

Student

Contact Information for Business Card

Tomas Bilbrea
Managing Director
tomas@kelvarin.com.au
www.kelvoria.com.au
+61 491058264
Melbourne, Australia

Font styles to use
Serif
Sans Serif

Colors

Designer to choose colors to be used in the design.

Requirements
Must have
• Horizontal design
• Standard business card size and shape. If font uses green or yellow colours, they will have to match the ones from the logo
Nice to have
• UPDATE: Use the contents of the green image to design one of the card sides. Use our logo in the background of that side as watermark.
• Passport image, or immigration stamps. A picture of the Yarra River (from Melbourne) would be cool as well.
Should not have
• Non-standard business card size and shape
• Not black as the background colour of any sides as we are not a VIP agency or a hight class service. We are orientes to young people and they like colours, pictures, something attractive.
• Vertical design
• NO YELLOW or BLACK AS THE BACKGROUND COLOUR OF ANY SIDE OF THE BIZ CARD

```html
<!DOCTYPE html>
<html lang="es">
<head>
<meta charset="utf-8">
<title>Coastal Learner Bureau — business cards</title>
<link rel="stylesheet" href="https://fonts.googleapis.com/css2?family=Open+Sans:wght@400;600;700&display=swap">
<style>
  :root {
    --bg: #e6e8ea;
    --brand-green: #0b5e3c;
    --brand-yellow: #e4bb1e;
    --paper: #ffffff;
    --ink: #1d1d1d;
    --muted: #4a4a4a;
    --shadow: 0 10px 28px rgba(0, 0, 0, 0.22);
  }
  * { margin: 0; padding: 0; box-sizing: border-box; }
  html, body {
    width: 1200px; height: 863px; overflow: hidden;
    background: var(--bg);
    font-family: "Open Sans", Arial, sans-serif;
  }
  .sheet { position: relative; width: 1200px; height: 863px; }

  .card {
    position: absolute;
    width: 560px; height: 320px;
    border-radius: 4px;
    overflow: hidden;
    box-shadow: var(--shadow);
  }

  /* Front side */
  .card--front { left: 150px; top: 80px; background: var(--brand-green); }
  .front__brand {
    position: absolute; left: 0; right: 0; top: 92px;
    display: flex; align-items: center; justify-content: center; gap: 14px;
    color: var(--paper);
    font-size: 52px; font-weight: 700; letter-spacing: 0.5px;
  }
  .front__mark {
    width: 26px; height: 26px; border-radius: 50%;
    background: var(--paper);
  }
  .front__band {
    position: absolute; left: 0; right: 0; bottom: 0; height: 92px;
    background: var(--paper);
    display: flex; align-items: center; justify-content: center;
  }
  .front__tagline {
    color: var(--brand-green);
    font-size: 19px; font-weight: 700;
  }

  /* Back side */
  .card--back { left: 490px; top: 470px; background: var(--paper); }
  .back__brand {
    position: absolute; right: 46px; top: 52px;
    display: flex; align-items: center; gap: 12px;
    color: var(--brand-green);
    font-size: 44px; font-weight: 700;
  }
  .back__mark {
    width: 22px; height: 22px; border-radius: 50%;
    background: var(--brand-yellow);
  }
  .holder { position: absolute; left: 40px; top: 140px; }
  .holder__name {
    color: var(--brand-green);
    font-size: 21px; font-weight: 700; line-height: 1.2;
  }
  .holder__role {
    color: var(--ink);
    font-size: 13px; font-weight: 400;
  }
  .back__rule {
    position: absolute; left: 170px; right: 46px; top: 184px;
    height: 2px; background: var(--brand-green);
  }
  .contact {
    position: absolute; right: 46px; top: 200px;
    list-style: none; text-align: right;
    color: var(--ink); font-size: 15px; line-height: 25px;
  }
  .contact__item { display: flex; align-items: center; justify-content: flex-end; gap: 10px; }
  .contact__icon { width: 14px; height: 14px; fill: var(--brand-green); }
  .contact__spacer { width: 14px; height: 14px; }
</style>
</head>
<body>
<main class="sheet">

  <section class="card card--front" aria-label="Card front">
    <div class="front__brand">
      <span class="front__mark" aria-hidden="true"></span>
      <span class="front__name">Kelvoria</span>
    </div>
    <div class="front__band">
      <p class="front__tagline">Hacemos más por ti!</p>
    </div>
  </section>

  <section class="card card--back" aria-label="Card back">
    <div class="back__brand">
      <span class="back__mark" aria-hidden="true"></span>
      <span class="back__name">Kelvoria</span>
    </div>

    <div class="holder">
      <p class="holder__name">Tomas Bilbrea</p>
      <p class="holder__role">Managing Director</p>
    </div>
    <div class="back__rule"></div>

    <ul class="contact">
      <li class="contact__item">+61 491058264
        <svg class="contact__icon" viewBox="0 0 24 24" aria-hidden="true"><path d="M6.6 10.8a15.2 15.2 0 0 0 6.6 6.6l2.2-2.2c.3-.3.7-.4 1-.2 1.1.4 2.3.6 3.6.6.6 0 1 .4 1 1V20c0 .6-.4 1-1 1C10.6 21 3 13.4 3 4c0-.6.4-1 1-1h3.5c.6 0 1 .4 1 1 0 1.3.2 2.5.6 3.6.1.3 0 .7-.2 1z"/></svg>
      </li>
      <li class="contact__item">tomas@kelvarin.com.au
        <svg class="contact__icon" viewBox="0 0 24 24" aria-hidden="true"><path d="M2 5h20v14H2zm2 2v.5l8 5 8-5V7l-8 5z"/></svg>
      </li>
      <li class="contact__item">www.kelvoria.com.au
        <svg class="contact__icon" viewBox="0 0 24 24" aria-hidden="true"><path d="M12 2a10 10 0 1 0 0 20 10 10 0 0 0 0-20zm6.9 6h-3a15 15 0 0 0-1.3-3.9A8 8 0 0 1 18.9 8zM12 4c.8 1.2 1.5 2.5 1.9 4h-3.8c.4-1.5 1.1-2.8 1.9-4zM4.3 14a8 8 0 0 1 0-4h3.4a16 16 0 0 0 0 4zm.8 2h3a15 15 0 0 0 1.3 3.9A8 8 0 0 1 5.1 16zm3-8h-3a8 8 0 0 1 4.3-3.9C8.8 5.3 8.4 6.6 8.1 8zM12 20c-.8-1.2-1.5-2.5-1.9-4h3.8c-.4 1.5-1.1 2.8-1.9 4zm2.3-6H9.7a14 14 0 0 1 0-4h4.6a14 14 0 0 1 0 4zm.3 5.9c.6-1.2 1-2.5 1.3-3.9h3a8 8 0 0 1-4.3 3.9zm1.7-5.9a16 16 0 0 0 0-4h3.4a8 8 0 0 1 0 4z"/></svg>
      </li>
      <li class="contact__item">Melbourne, Australia <span class="contact__spacer"></span></li>
    </ul>
  </section>

</main>
</body>
</html>
```